Webdesign für Wabenhof
Zielgruppe
Imkerei, Verkauf von Honig und Honigerzeugnissen, so wie Bienenwachskerzen.
Zielgruppe sind vermutlich Frauen im mittleren bis gehobenen Alter.
Aufgabenstellung
Es gibt ein Firmenlogo.
Ich bevorzuge als Grundfarbe weiß, lasse mich aber von guten Einfällen gerne überraschen.
Die Website www.kelvaroni.at finde ich sehr ansprechend.
Nur ohne Musik.
Ohne Deutsch/Englisch Auswahl.
Es soll danach Word press verwendet werden.

```html
<!DOCTYPE html>
<html lang="de">
<head>
<meta charset="utf-8">
<title>Wabenhof Waldtal – Der Shop</title>
<link href="https://fonts.googleapis.com/css2?family=Roboto:ital,wght@0,400;0,500;0,700;1,400&family=Roboto+Condensed:wght@400;700&family=Lato:wght@300;400&display=swap" rel="stylesheet">
<style>
:root{
  --stage:#f1f1f1;
  --page:#ffffff;
  --line:#e6e6e6;
  --ink:#333333;
  --muted:#8a8a8a;
  --honey:#f2a02b;
  --brown:#5a3414;
  --link:#27a9e1;
  --tile:#e9e9e9;
}
*{box-sizing:border-box;margin:0;padding:0}
html,body{width:683px;height:1200px;overflow:hidden}
body{background:var(--stage);font-family:"Roboto",sans-serif;color:var(--ink);position:relative}
.page{position:absolute;left:32px;top:32px;width:619px;height:1133px;background:var(--page)}
.topbar{position:absolute;left:0;top:0;width:619px;height:15px;border-bottom:1px solid var(--line)}
.topbar .item{position:absolute;top:0;height:15px;border-left:1px solid var(--line);font-size:3.6px;letter-spacing:.4px;line-height:15px;text-align:center;color:#444}
.header{position:absolute;left:0;top:15px;width:619px;height:52px;border-bottom:1px solid var(--line)}
.nav a{position:absolute;top:36px;font-family:"Roboto Condensed",sans-serif;font-size:4.2px;letter-spacing:.6px;color:#777;text-decoration:none}
.nav a.active{color:var(--honey)}
.brand{position:absolute;left:268px;top:2px;width:84px;text-align:center}
.brand .mark{display:block;margin:0 auto 3px}
.brand .name{font-family:"Roboto Condensed",sans-serif;font-weight:700;font-size:6.5px;color:var(--brown);letter-spacing:.3px}
.brand .sub{font-family:"Roboto Condensed",sans-serif;font-size:4px;color:var(--honey);letter-spacing:1.8px;margin-top:1px}
.banner{position:absolute;left:114px;top:78px;width:387px;height:55px;background:linear-gradient(90deg,#6a7a55 0%,#8f8fb0 25%,#51446e 45%,#9c94b8 65%,#564d7b 85%,#6f8756 100%)}
.toolbar{position:absolute;left:118px;top:144px;height:13px;display:flex;gap:3px}
.toolbar .ctl{border:1px solid var(--line);height:13px;font-size:3.8px;line-height:11px;padding:0 4px;display:flex;align-items:center;justify-content:space-between;color:#333}
.grid{position:absolute;left:118px;top:169px;display:grid;grid-template-columns:repeat(4,91px);column-gap:4.3px;row-gap:4px}
.card{border:1px solid var(--line);height:156px;background:#fff}
.card .photo{height:91px;background:var(--tile);position:relative}
.card .photo span{position:absolute;left:25px;top:18px;width:42px;height:56px;border-radius:3px}
.vanille span{background:linear-gradient(180deg,#2a2a2a 0 10%,#f3dc5a 10%,#e4c53a 100%)}
.orange span{background:linear-gradient(180deg,#2a2a2a 0 10%,#f3a52a 10%,#d9861a 100%)}
.karamell span{background:linear-gradient(180deg,#2a2a2a 0 10%,#c66a2a 10%,#a14e1c 100%)}
.card .body{padding:7px 5px 0}
.card h3{font-weight:400;font-size:4.6px;color:#333}
.card .row{display:flex;justify-content:space-between;align-items:flex-end;margin-top:6px}
.card .price{color:var(--honey);font-size:5.8px}
.card .stars{color:#aaa;font-size:4.4px;letter-spacing:-.3px}
.card .meta{font-size:3.2px;color:#333;margin-top:2px;line-height:7px}
.card .meta a{color:var(--link);text-decoration:none}
.card .actions{border-top:1px solid var(--line);margin-top:4px;padding-top:6px;display:flex;justify-content:space-between;font-size:3.6px;font-style:italic;color:#333}
.newsletter{position:absolute;left:118px;top:679px;width:387px;height:97px;background:linear-gradient(90deg,#f4f4f3,#ececeb 60%,#dedede)}
.newsletter h2{font-family:"Lato",sans-serif;font-weight:300;font-size:9px;letter-spacing:.6px;text-align:center;margin-top:30px;color:#333}
.newsletter form{display:flex;justify-content:center;margin-top:9px}
.newsletter .field{width:110px;height:14px;border:1px solid #d6d6d6;background:#fff;font-size:3.8px;color:#999;line-height:12px;padding-left:6px}
.newsletter .send{width:58px;height:14px;margin-left:2px;background:var(--honey);color:#fff;font-size:3.8px;letter-spacing:.8px;line-height:14px;text-align:center}
.about{position:absolute;left:150px;top:796px;width:323px}
.about h2{font-family:"Lato",sans-serif;font-weight:300;font-size:9px;letter-spacing:.9px;text-align:center;color:#333;margin-bottom:19px}
.about h4{font-size:3.9px;font-weight:500;color:#222;margin-bottom:2px}
.about p{font-size:3.7px;line-height:7px;color:#888;margin-bottom:10px;text-align:justify}
.divider{position:absolute;left:114px;top:948px;width:387px;height:1.2px;background:var(--honey)}
.footer{position:absolute;left:118px;top:962px;width:387px;display:grid;grid-template-columns:repeat(4,96.7px)}
.footer h5{font-size:4.2px;font-weight:500;color:#222;margin-bottom:11px}
.footer li{list-style:none;font-size:3.7px;color:#888;line-height:7.7px}
.footer p{font-size:3.7px;color:#888;line-height:7.7px}
.footer b{color:#333;font-weight:500}
.social{display:flex;gap:6px;margin-top:10px}
.social i{width:4px;height:4px;border-radius:50%;background:#555;display:block}
.bottom{position:absolute;left:0;top:1070px;width:619px;border-top:1px solid var(--line);text-align:center}
.bottom p{font-size:3.7px;color:#999;margin-top:14px}
.pay{display:flex;justify-content:center;gap:4px;margin-top:6px}
.pay i{display:block;width:17.5px;height:10px;border:1px solid #ddd;background:#fafafa}
</style>
</head>
<body>
<div class="page">
  <div class="topbar">
    <div class="item" style="left:393px;width:43px">MEIN KONTO ⌄</div>
    <div class="item" style="left:436px;width:64px;border-right:1px solid var(--line)">▾ WARENKORB</div>
  </div>

  <header class="header">
    <nav class="nav">
      <a style="left:133px">STARTSEITE</a>
      <a style="left:179px">DIE MANUFAKTUR</a>
      <a style="left:238px">DER HONIG</a>
      <a style="left:352px">DAS BIENENWACHS</a>
      <a class="active" style="left:418px">DER SHOP</a>
      <a style="left:465px">KONTAKT</a>
    </nav>
    <div class="brand">
      <svg class="mark" width="8" height="8" viewBox="0 0 8 8"><rect width="8" height="8" fill="var(--honey)"/></svg>
      <div class="name">WABENHOF</div>
      <div class="sub">WALDTAL</div>
    </div>
  </header>

  <div class="banner" role="img" aria-label="Fotobanner: Biene auf Lavendelblüten"></div>

  <div class="toolbar">
    <div class="ctl" style="width:60px">Preis aufsteigend <span>⌄</span></div>
    <div class="ctl" style="width:13px;justify-content:center">↑</div>
    <div class="ctl" style="width:60px">Honig im Glas <span>⌄</span></div>
    <div class="ctl" style="width:26px;justify-content:space-around">▦ ☰</div>
  </div>

  <div class="grid">
    <article class="card"><div class="photo vanille" role="img" aria-label="Produktfoto: Honigglas Vanille"><span></span></div><div class="body"><h3>Honig mit Vanille</h3><div class="row"><span class="price">€6,95</span><span class="stars">★★★★★</span></div><div class="meta">Grundpreis: €5,95 /100g<br>Inkl. Mwst.; zzgl. <a>Versandkosten</a></div><div class="actions"><span>▾ In den Warenkorb legen</span><span>☰ Details</span></div></div></article>
    <article class="card"><div class="photo orange" role="img" aria-label="Produktfoto: Honigglas Orange"><span></span></div><div class="body"><h3>Honig mit Orange</h3><div class="row"><span class="price">€6,95</span><span class="stars">★★★★★</span></div><div class="meta">Grundpreis: €5,95 /100g<br>Inkl. Mwst.; zzgl. <a>Versandkosten</a></div><div class="actions"><span>▾ In den Warenkorb legen</span><span>☰ Details</span></div></div></article>
    <article class="card"><div class="photo karamell" role="img" aria-label="Produktfoto: Honigglas Karamell"><span></span></div><div class="body"><h3>Honig mit Karamell</h3><div class="row"><span class="price">€6,95</span><span class="stars">★★★★★</span></div><div class="meta">Grundpreis: €5,95 /100g<br>Inkl. Mwst.; zzgl. <a>Versandkosten</a></div><div class="actions"><span>▾ In den Warenkorb legen</span><span>☰ Details</span></div></div></article>
    <article class="card"><div class="photo vanille" role="img" aria-label="Produktfoto: Honigglas Vanille"><span></span></div><div class="body"><h3>Honig mit Vanille</h3><div class="row"><span class="price">€6,95</span><span class="stars">★★★★★</span></div><div class="meta">Grundpreis: €5,95 /100g<br>Inkl. Mwst.; zzgl. <a>Versandkosten</a></div><div class="actions"><span>▾ In den Warenkorb legen</span><span>☰ Details</span></div></div></article>
    <article class="card"><div class="photo vanille" role="img" aria-label="Produktfoto: Honigglas Vanille"><span></span></div><div class="body"><h3>Honig mit Vanille</h3><div class="row"><span class="price">€6,95</span><span class="stars">★★★★★</span></div><div class="meta">Grundpreis: €5,95 /100g<br>Inkl. Mwst.; zzgl. <a>Versandkosten</a></div><div class="actions"><span>▾ In den Warenkorb legen</span><span>☰ Details</span></div></div></article>
    <article class="card"><div class="photo orange" role="img" aria-label="Produktfoto: Honigglas Orange"><span></span></div><div class="body"><h3>Honig mit Orange</h3><div class="row"><span class="price">€6,95</span><span class="stars">★★★★★</span></div><div class="meta">Grundpreis: €5,95 /100g<br>Inkl. Mwst.; zzgl. <a>Versandkosten</a></div><div class="actions"><span>▾ In den Warenkorb legen</span><span>☰ Details</span></div></div></article>
    <article class="card"><div class="photo karamell" role="img" aria-label="Produktfoto: Honigglas Karamell"><span></span></div><div class="body"><h3>Honig mit Karamell</h3><div class="row"><span class="price">€6,95</span><span class="stars">★★★★★</span></div><div class="meta">Grundpreis: €5,95 /100g<br>Inkl. Mwst.; zzgl. <a>Versandkosten</a></div><div class="actions"><span>▾ In den Warenkorb legen</span><span>☰ Details</span></div></div></article>
    <article class="card"><div class="photo vanille" role="img" aria-label="Produktfoto: Honigglas Vanille"><span></span></div><div class="body"><h3>Honig mit Vanille</h3><div class="row"><span class="price">€6,95</span><span class="stars">★★★★★</span></div><div class="meta">Grundpreis: €5,95 /100g<br>Inkl. Mwst.; zzgl. <a>Versandkosten</a></div><div class="actions"><span>▾ In den Warenkorb legen</span><span>☰ Details</span></div></div></article>
    <article class="card"><div class="photo vanille" role="img" aria-label="Produktfoto: Honigglas Vanille"><span></span></div><div class="body"><h3>Honig mit Vanille</h3><div class="row"><span class="price">€6,95</span><span class="stars">★★★★★</span></div><div class="meta">Grundpreis: €5,95 /100g<br>Inkl. Mwst.; zzgl. <a>Versandkosten</a></div><div class="actions"><span>▾ In den Warenkorb legen</span><span>☰ Details</span></div></div></article>
    <article class="card"><div class="photo orange" role="img" aria-label="Produktfoto: Honigglas Orange"><span></span></div><div class="body"><h3>Honig mit Orange</h3><div class="row"><span class="price">€6,95</span><span class="stars">★★★★★</span></div><div class="meta">Grundpreis: €5,95 /100g<br>Inkl. Mwst.; zzgl. <a>Versandkosten</a></div><div class="actions"><span>▾ In den Warenkorb legen</span><span>☰ Details</span></div></div></article>
    <article class="card"><div class="photo karamell" role="img" aria-label="Produktfoto: Honigglas Karamell"><span></span></div><div class="body"><h3>Honig mit Karamell</h3><div class="row"><span class="price">€6,95</span><span class="stars">★★★★★</span></div><div class="meta">Grundpreis: €5,95 /100g<br>Inkl. Mwst.; zzgl. <a>Versandkosten</a></div><div class="actions"><span>▾ In den Warenkorb legen</span><span>☰ Details</span></div></div></article>
  </div>

  <section class="newsletter" role="img" aria-label="Hintergrund: blasses Foto von Bienen">
    <h2>JETZT FÜR UNSEREN AKTUELLEN NEWSLETTER ANMELDEN</h2>
    <form><div class="field">E-Mail Adresse hier eingeben ...</div><div class="send">ABSENDEN</div></form>
  </section>

  <section class="about">
    <h2>EXKLUSIVER HONIG AUS DEM WALDTAL</h2>
    <h4>Lorem ipsum dolor sit amet, consetetur sadipscing elitr, sed diam nonumy eirmod tempor invidunt</h4>
    <p>Lorem ipsum dolor sit amet, consetetur sadipscing elitr, sed diam nonumy eirmod tempor invidunt ut labore et dolore magna aliquyam erat, sed diam voluptua. At vero eos et accusam et justo duo dolores et ea rebum. Stet clita kasd gubergren, no sea takimata sanctus est Lorem ipsum dolor sit amet. Lorem ipsum dolor sit amet, consetetur sadipscing elitr, sed diam nonumy eirmod tempor invidunt ut labore et dolore magna aliquyam erat, sed diam voluptua. At vero eos et accusam et justo duo dolores et ea rebum. Stet clita kasd gubergren, no sea takimata sanctus est Lorem ipsum dolor sit amet. Lorem ipsum dolor sit amet, consetetur sadipscing elitr, sed diam nonumy eirmod tempor invidunt ut labore.</p>
    <h4>Lorem ipsum dolor sit amet, consetetur sadipscing elitr, sed diam nonumy eirmod tempor invidunt</h4>
    <p>Lorem ipsum dolor sit amet, consetetur sadipscing elitr, sed diam nonumy eirmod tempor invidunt ut labore et dolore magna aliquyam erat, sed diam voluptua. At vero eos et accusam et justo duo dolores et ea rebum. Stet clita kasd gubergren, no sea takimata sanctus est Lorem ipsum dolor sit amet. Lorem ipsum dolor sit amet, consetetur sadipscing elitr, sed diam nonumy eirmod tempor invidunt ut labore et dolore magna aliquyam erat, sed diam voluptua. At vero eos et accusam et justo duo dolores et ea rebum. Stet clita kasd gubergren, no sea takimata sanctus est Lorem ipsum dolor sit amet. Lorem ipsum dolor sit amet, consetetur sadipscing elitr, sed diam nonumy eirmod tempor invidunt ut labore et.</p>
  </section>

  <div class="divider"></div>

  <footer class="footer">
    <div>
      <h5>Wabenhof © 2018</h5>
      <p>Lorem ipsum dolor sit amet, consetetur sadipscing elitr, sed diam nonumy eirmod tempor invidunt ut labore et dolore magna aliquyam erat, sed diam voluptua. Lorem ipsum dolor sit amet, consetetur sadipscing</p>
      <p style="margin-top:7px"><b>Telefon:</b> 0000 000 0000<br><b>E-Mail:</b> service@wabenhof-waldtal.de</p>
      <div class="social"><i></i><i></i><i></i><i></i><i></i></div>
    </div>
    <div><h5>Unternehmen</h5><ul><li>Die Manufaktur</li><li>Der Honig</li><li>Das Bienenwachs</li><li>Kontaktformular</li><li>Datenschutz</li><li>Impressum</li></ul></div>
    <div><h5>Service</h5><ul><li>FAQ</li><li>Lieferung &amp; Versand</li><li>AGB</li><li>Widerrufsbelehrung</li><li>Widerrufsformular</li><li>Glossar</li><li>Kundenmeinungen</li></ul></div>
    <div><h5>Mein Konto</h5><ul><li>Kundenkonto anlegen</li><li>Meine Bestellungen</li><li>Meine Nachrichten</li><li>Mein Wunschzettel</li><li>Produkte vergleichen</li></ul></div>
  </footer>

  <div class="bottom">
    <p>Copyright © 2018 Wabenhof | Musterstraße 10 | 12345 Musterstadt | Tel. 012 345 678 | Fax 012 345 678 | info@wabenhof-waldtal.de</p>
    <div class="pay"><i></i><i></i><i></i><i></i><i></i></div>
  </div>
</div>
</body>
</html>
```